Professional & attention grabbing.

A business card design, front and back. I already have a logo I will attach, but I am open to something new as well.
Things to include:
Name:
Title:
Phone:
Email:
Wanting something that is professional but attention grabbing.
Also we do a lot of work using drones on natural gas pipelines (leading the future)if you want to include any of that. I'm open to ideas.
Target Market(s)
Natural gas transmission industry / greenhouse gas mitigation industry
Industry/Entity Type
Business
Colors
Designer to choose colors to be used in the design.
Look and feel
Each slider illustrates characteristics of the customer's brand and the style your logo design should communicate.

```html
<!DOCTYPE html>
<html lang="en">
<head>
<meta charset="utf-8">
<title>Corvale Inspections – Business Cards</title>
<link rel="stylesheet" href="https://fonts.googleapis.com/css2?family=Montserrat:wght@500;700&display=swap">
<style>
  :root {
    --backdrop: #1b1b1c;
    --card-dark: #39393b;
    --card-light: #ffffff;
    --brand-red: #c0202a;
    --ink: #2f2f31;
    --ink-soft: #4a4a4c;
    --white: #ffffff;
  }
  * { box-sizing: border-box; margin: 0; padding: 0; }
  html, body {
    width: 1200px; height: 1000px; overflow: hidden;
    background: var(--backdrop);
    font-family: "Montserrat", Arial, sans-serif;
  }
  .canvas { position: relative; width: 1200px; height: 1000px; }

  .card {
    position: absolute;
    width: 700px; height: 400px;
    border-radius: 34px;
    display: flex; align-items: center;
  }
  .card--front {
    left: 110px; top: 90px;
    background: var(--card-dark);
    justify-content: center;
  }
  .card--back {
    left: 390px; top: 510px;
    background: var(--card-light);
    padding-left: 70px;
  }

  .brand { display: flex; align-items: center; gap: 16px; }
  .brand__mark { width: 40px; height: 40px; background: var(--brand-red); flex: none; }
  .brand__name {
    font-weight: 700; font-size: 44px; letter-spacing: -0.5px;
    line-height: 1;
  }
  .card--front .brand__name { color: var(--white); }
  .card--back .brand__name { color: var(--ink); font-size: 30px; }
  .card--back .brand__mark { width: 28px; height: 28px; }
  .card--back .brand { gap: 12px; }

  .divider {
    width: 2px; height: 130px; background: var(--brand-red);
    margin: 0 26px 0 24px; flex: none;
  }

  .contact { display: flex; flex-direction: column; }
  .contact__name {
    color: var(--brand-red); font-weight: 700; font-size: 26px;
    text-transform: uppercase; line-height: 1.05;
  }
  .contact__title {
    color: var(--ink); font-weight: 700; font-size: 15px;
    text-transform: uppercase; margin-bottom: 12px;
  }
  .contact__line {
    display: flex; align-items: center; gap: 10px;
    color: var(--ink-soft); font-weight: 500; font-size: 17px;
    line-height: 1.45;
  }
  .contact__icon { width: 14px; height: 14px; flex: none; fill: var(--brand-red); }
</style>
</head>
<body>
<main class="canvas">
  <section class="card card--front" aria-label="Card front">
    <div class="brand">
      <span class="brand__mark"></span>
      <span class="brand__name">Corvale Inspections</span>
    </div>
  </section>

  <section class="card card--back" aria-label="Card back">
    <div class="brand">
      <span class="brand__mark"></span>
      <span class="brand__name">Corvale<br>Inspections</span>
    </div>
    <span class="divider"></span>
    <div class="contact">
      <p class="contact__name">Daniel Hart</p>
      <p class="contact__title">Founder</p>
      <p class="contact__line">
        <svg class="contact__icon" viewBox="0 0 16 16" aria-hidden="true">
          <path d="M3.6 1.2l2.2 2.6c.3.4.3.9 0 1.3L4.7 6.4c.9 2 2.8 3.9 4.9 4.9l1.3-1.1c.4-.3.9-.3 1.3 0l2.6 2.2c.4.3.4.9.1 1.3l-1.4 1.5c-.5.5-1.3.7-2 .4C6 14 2 10 .4 4.6c-.2-.7 0-1.5.5-2L2.3 1.1c.4-.3 1-.3 1.3.1z"/>
        </svg>
        000 000 0000
      </p>
      <p class="contact__line">
        <svg class="contact__icon" viewBox="0 0 16 16" aria-hidden="true">
          <path d="M1 3h14v1.2L8 8.6 1 4.2z M1 5.8l7 4.4 7-4.4V13H1z"/>
        </svg>
        info@yourmail.com
      </p>
    </div>
  </section>
</main>
</body>
</html>
```